New Business Card Design Project

We require a business card design for Vexalund, a newly established Indian company.
Our focus is on the development, manufacturing, and export of a diverse array of pharmaceutical products on a global scale. The card should convey a professional appearance, as our primary markets are in Africa, China, and Southeast Asian nations.
We envision a two-sided business card, with the reverse side dedicated to a logo set against a solid color or an elegantly designed pattern. The corners should be rounded. We would appreciate seeing both horizontal and vertical design options. We trust the designer to utilize their expertise in creating this design.

The content for the business card is included in the attached Word file.

Target Market(s)

Our primary markets are in Africa, China, and Southeast Asian, Latin America, Maldives, Sri Lanka

Industry/Entity Type

Pharmaceutical Manufacturing and Export

Contact Information for Business Card

Colors

Designer to choose colors to be used in the design.

Requirements
Must have
• The reverse side of the business card features solely the logo along with the tagline, "Care That Heals."
Should not have
• The logo should not exceed two instances, encompassing both the front and back sides of the card.

```html
<!DOCTYPE html>
<html lang="en">
<head>
<meta charset="UTF-8">
<title>Vexalund – Business Card</title>
<link href="https://fonts.googleapis.com/css2?family=Montserrat:wght@400;500;700;800&display=swap" rel="stylesheet">
<style>
  :root {
    --stage: #2e2e30;
    --card: #f7f7f7;
    --brand-blue: #2199d3;
    --brand-red: #e2563f;
    --red-deep: #9c2f1c;
    --red-mid: #c4422a;
    --ink: #3a3a3a;
    --rule: #ef8a72;
  }
  * { margin: 0; padding: 0; box-sizing: border-box; }
  html, body { width: 1200px; height: 900px; overflow: hidden; }
  body {
    background: var(--stage);
    font-family: "Montserrat", sans-serif;
    color: var(--ink);
    display: flex;
    align-items: center;
    justify-content: center;
    gap: 80px;
  }
  .card {
    position: relative;
    width: 380px;
    height: 640px;
    border-radius: 34px;
    background: linear-gradient(160deg, #ffffff 0%, var(--card) 60%, #ececec 100%);
    overflow: hidden;
  }
  .brand {
    display: flex;
    align-items: center;
    justify-content: center;
    gap: 12px;
  }
  .brand-dot {
    width: 22px; height: 22px;
    border-radius: 50%;
    background: var(--brand-red);
  }
  .brand-name {
    font-weight: 800;
    color: var(--brand-blue);
    font-size: 52px;
    letter-spacing: -0.5px;
  }
  .card-front .brand { margin-top: 104px; }
  .holder {
    text-align: center;
    margin-top: 46px;
  }
  .holder-name {
    color: var(--brand-blue);
    font-weight: 700;
    font-size: 17px;
    letter-spacing: 0.5px;
    text-transform: uppercase;
  }
  .holder-role { font-size: 15px; margin-top: 2px; }
  .rule {
    height: 1px;
    width: 250px;
    margin: 20px auto;
    background: linear-gradient(90deg, transparent, var(--rule), transparent);
  }
  .contacts {
    list-style: none;
    width: 250px;
    margin: 0 auto;
    font-size: 14.5px;
    line-height: 1.55;
  }
  .contacts li { display: flex; align-items: center; gap: 9px; }
  .contacts svg { width: 15px; height: 15px; flex: none; }
  .address {
    text-align: center;
    font-size: 15px;
    line-height: 1.45;
  }
  .band {
    position: absolute;
    left: 0; bottom: 0;
    width: 380px; height: 170px;
  }
  .band-text {
    font-family: "Montserrat", sans-serif;
    font-weight: 700;
    font-size: 15px;
    letter-spacing: 2px;
    fill: #ffffff;
  }
  .card-back .brand {
    position: absolute;
    left: 0; right: 0;
    top: 300px;
  }
</style>
</head>
<body>

<section class="card card-front" aria-label="Front of card">
  <div class="brand">
    <span class="brand-dot"></span>
    <span class="brand-name">Vexalund</span>
  </div>

  <div class="holder">
    <p class="holder-name">Ravindra K. Solanki</p>
    <p class="holder-role">CEO Of Vexalund</p>
  </div>

  <div class="rule"></div>

  <ul class="contacts">
    <li>
      <svg viewBox="0 0 16 16" fill="none" stroke="var(--brand-blue)" stroke-width="1.4"><rect x="4" y="1" width="8" height="14" rx="1.5"/><line x1="7" y1="12.5" x2="9" y2="12.5"/></svg>
      +919812345670
    </li>
    <li>
      <svg viewBox="0 0 16 16" fill="var(--brand-blue)"><path d="M1 3h14v10H1z"/><path d="M1 3l7 5 7-5" fill="none" stroke="#fff" stroke-width="1.2"/></svg>
      rsolanki@vexalund.com
    </li>
    <li>
      <svg viewBox="0 0 16 16" fill="none" stroke="var(--brand-blue)" stroke-width="1.2"><circle cx="8" cy="8" r="6.5"/><ellipse cx="8" cy="8" rx="3" ry="6.5"/><line x1="1.5" y1="8" x2="14.5" y2="8"/><line x1="2.5" y1="4.8" x2="13.5" y2="4.8"/><line x1="2.5" y1="11.2" x2="13.5" y2="11.2"/></svg>
      www.vexalund.com
    </li>
  </ul>

  <div class="rule"></div>

  <p class="address">14, Sarovar Nagar<br>Wardha, 442001, India</p>

  <svg class="band" viewBox="0 0 380 170">
    <defs>
      <linearGradient id="bandFill" x1="0" y1="1" x2="1" y2="0">
        <stop offset="0" stop-color="var(--red-deep)"/>
        <stop offset="0.5" stop-color="var(--brand-red)"/>
        <stop offset="1" stop-color="var(--red-deep)"/>
      </linearGradient>
      <path id="frontArc" d="M70 150 Q200 60 360 60"/>
    </defs>
    <path d="M0 170 L0 140 Q170 20 380 22 L380 170 Z" fill="url(#bandFill)"/>
    <path d="M0 140 Q170 20 380 22" fill="none" stroke="var(--red-mid)" stroke-width="3"/>
    <text class="band-text"><textPath href="#frontArc" startOffset="50%" text-anchor="middle">CARE THAT HEALS</textPath></text>
  </svg>
</section>

<section class="card card-back" aria-label="Back of card">
  <div class="brand">
    <span class="brand-dot"></span>
    <span class="brand-name">Vexalund</span>
  </div>

  <svg class="band" viewBox="0 0 380 170">
    <defs>
      <linearGradient id="bandFillBack" x1="0" y1="1" x2="1" y2="0">
        <stop offset="0" stop-color="var(--red-deep)"/>
        <stop offset="0.5" stop-color="var(--brand-red)"/>
        <stop offset="1" stop-color="var(--red-deep)"/>
      </linearGradient>
      <path id="backArc" d="M70 150 Q200 60 360 60"/>
    </defs>
    <path d="M0 170 L0 140 Q170 20 380 22 L380 170 Z" fill="url(#bandFillBack)"/>
    <path d="M0 140 Q170 20 380 22" fill="none" stroke="var(--red-mid)" stroke-width="3"/>
    <text class="band-text"><textPath href="#backArc" startOffset="50%" text-anchor="middle">CARE THAT HEALS</textPath></text>
  </svg>
</section>

</body>
</html>
```